Form With Marla - Health and Wellness Business Card and Logo

I need a business card design with a logo for my business you can check out at www.formwithmarla.net. I want something more original, simplistic, and memorable than the basic logo I have on my site currently. I am a health and wellness coach and I offer mindset coaching and nutrition plans. I like the colour teal and dark grey/black for my theme colours. I emphasize growth, longterm change, and the whole package of "healthy mind, healthy body, healthy life". I had played around the idea of intertwining 3 M's or incorporating growth (leaves etc.) into my design. I want my expertise and experience to show through. In one glance I want people to understand with confidence I can help them accomplish anything they set their minds to. I look forward to seeing what everyone comes up with!

Industry/Entity Type

Health And Wellness

Contact Information for Business Card

Form With Marla
Marla Prentiss
BSc, Health & Wellness Coach
"Manifest your best"
www.formwithmarla.net
formwithmarla@quillpost.net
472-618-9043

Colors
33b8a4
ffffff
333333
000000

Requirements
Must have
• A memorable and unique logo for my business!
Nice to have
• Could have the phrase "Are you unhappy with your body and state of health?" or "It takes the right skills to develop habits in order to create long term change. I can help you get there."

```html
<!DOCTYPE html>
<html lang="en">
<head>
<meta charset="utf-8">
<title>Form With Marla – Business Card</title>
<link rel="stylesheet" href="https://fonts.googleapis.com/css2?family=Didact+Gothic&family=Open+Sans:wght@400;700&display=swap">
<style>
  :root {
    --teal: #1f8a84;
    --teal-soft: #33b8a4;
    --card-dark: #262626;
    --ink: #333333;
    --paper: #ffffff;
    --backdrop: #3a3a3a;
  }
  * { box-sizing: border-box; margin: 0; padding: 0; }
  html, body { width: 1200px; height: 1000px; overflow: hidden; }
  body {
    background: var(--backdrop);
    font-family: "Open Sans", sans-serif;
    position: relative;
  }
  .card {
    position: absolute;
    left: 250px;
    width: 700px;
    height: 400px;
    border-radius: 22px;
    overflow: hidden;
  }
  .card--back { top: 60px; background: var(--card-dark); }
  .card--front { top: 540px; background: var(--paper); }

  .brand-mark {
    position: absolute;
    top: 150px; left: 0; right: 0;
    text-align: center;
    font-family: "Didact Gothic", sans-serif;
    font-size: 42px;
    color: var(--paper);
    letter-spacing: 1px;
  }
  .brand-rule {
    position: absolute;
    top: 210px; left: 250px;
    width: 200px; height: 1px;
    background: #777;
  }
  .tagline {
    position: absolute;
    bottom: 50px; left: 0; right: 0;
    text-align: center;
    font-size: 17px;
    letter-spacing: 7px;
    color: var(--teal);
  }

  .front-title {
    position: absolute;
    top: 34px; left: 48px;
    font-family: "Didact Gothic", sans-serif;
    font-size: 46px;
    color: #111;
  }
  .name-tab {
    position: absolute;
    top: 128px; left: 0;
    width: 12px; height: 42px;
    background: var(--teal);
    border-radius: 0 4px 4px 0;
  }
  .person-name {
    position: absolute;
    top: 124px; left: 38px;
    font-weight: 700;
    font-size: 30px;
    color: var(--teal);
    letter-spacing: 0.5px;
  }
  .person-role {
    position: absolute;
    top: 166px; left: 38px;
    font-weight: 700;
    font-size: 15px;
    color: var(--ink);
  }
  .contact-list {
    position: absolute;
    top: 216px; left: 38px;
    list-style: none;
  }
  .contact-list li {
    display: flex;
    align-items: center;
    gap: 14px;
    height: 28px;
    font-size: 19px;
    color: var(--ink);
  }
  .contact-list svg { width: 16px; height: 16px; flex: none; }
  .contact-list .accent { color: var(--teal); }
  .social-dot {
    width: 16px; height: 16px;
    border-radius: 4px;
    background: var(--ink);
    flex: none;
  }
  .corner-mark {
    position: absolute;
    right: 44px; bottom: 40px;
    font-weight: 700;
    font-size: 22px;
    color: var(--teal);
  }
</style>
</head>
<body>
  <section class="card card--back">
    <div class="brand-mark">form with marla</div>
    <div class="brand-rule"></div>
    <p class="tagline">"Manifest your best"</p>
  </section>

  <section class="card card--front">
    <h1 class="front-title">form with marla</h1>
    <div class="name-tab"></div>
    <h2 class="person-name">MARLA PRENTISS</h2>
    <p class="person-role">BSc, Health &amp; Wellness Coach</p>
    <ul class="contact-list">
      <li>
        <svg viewBox="0 0 24 24" fill="var(--teal)"><path d="M6.6 10.8a15 15 0 0 0 6.6 6.6l2.2-2.2a1 1 0 0 1 1-.25 11.4 11.4 0 0 0 3.6.57 1 1 0 0 1 1 1V20a1 1 0 0 1-1 1A17 17 0 0 1 3 4a1 1 0 0 1 1-1h3.5a1 1 0 0 1 1 1c0 1.25.2 2.45.57 3.57a1 1 0 0 1-.25 1z"/></svg>
        472-618-9043
      </li>
      <li>
        <svg viewBox="0 0 24 24" fill="var(--teal)"><path d="M2 5h20v14H2z"/><path d="M2 5l10 8 10-8" fill="none" stroke="#fff" stroke-width="2"/></svg>
        formwithmarla@quillpost.net
      </li>
      <li>
        <svg viewBox="0 0 24 24" fill="none" stroke="var(--teal)" stroke-width="2"><circle cx="12" cy="12" r="10"/><path d="M2 12h20M12 2c3 3 3 17 0 20M12 2c-3 3-3 17 0 20"/></svg>
        <span>www.<span class="accent">formwithmarla</span>.net</span>
      </li>
      <li>
        <span class="social-dot"></span>
        @marlaprentiss
      </li>
    </ul>
    <div class="corner-mark">Form With Marla</div>
  </section>
</body>
</html>
```